Corporate-Design für Steuerberatungsgesellschaft
Zielgruppe
Wir sind eine Steuerberatungsgesellschaft mit 10 Mitarbeitern im Norden von Deutschland, kurz vor der Ostseeküste. Unser Unternehmen besteht seit 30 Jahren. Wir betreuen vor allem Mandanten in kleinen und mittleren Unternehmen: von der Arztpraxis bis zum Bauunternehmen. Demnächst werden wir neue Räume beziehen. Diese sollen großzügiger und moderner werden, teilweise mit Glaswänden.
Aufgabenstellung
Unser bisheriges Farbkonzept war von bordeaux und creme geprägt (www.kanzlei-mervato.de). Das muss aber nicht weiter bestehen. Das bisherige Logo finden wir inhaltlich recht treffend, aber es sollte moderner gestaltet werden. Der Schriftzug des Kanzleinamens soll an der Fassade in silbernen Buchstaben angebracht werden.

```html
<!DOCTYPE html>
<html lang="de">
<head>
<meta charset="utf-8">
<title>KLR Barsen Steuerberatung – Briefbogen</title>
<link href="https://fonts.googleapis.com/css2?family=Montserrat:wght@400;500;600;700&display=swap" rel="stylesheet">
<style>
  :root {
    --backdrop: #e4e8e4;
    --paper: #f5f5f5;
    --burgundy: #5e0d18;
    --ink: #3b3b3b;
    --ink-soft: #555555;
    --silver: #8a8a8a;
    --white: #ffffff;
  }
  * { margin: 0; padding: 0; box-sizing: border-box; }
  html, body {
    width: 1200px; height: 1012px; overflow: hidden;
    background: var(--backdrop);
    font-family: "Montserrat", sans-serif;
    color: var(--ink);
  }
  .letterhead {
    position: absolute; left: 260px; top: 26px;
    width: 679px; height: 960px;
    background: var(--paper);
    overflow: hidden;
  }
  .brand { position: absolute; left: 336px; top: 26px; display: flex; align-items: center; gap: 10px; }
  .brand-square { width: 56px; height: 62px; border: 4px solid var(--silver); border-radius: 8px; }
  .brand-name { font-weight: 500; color: var(--ink); line-height: 1; }
  .brand-name .firm { display: block; font-size: 40px; letter-spacing: 0.5px; }
  .brand-name .trade { display: block; font-size: 11px; letter-spacing: 9.4px; margin-top: 5px; }

  .fold-mark { position: absolute; left: 0; top: 337px; width: 4px; height: 1px; background: var(--ink); }

  .sender { position: absolute; left: 71px; top: 146px; font-size: 7.5px; }
  .sender .company { font-weight: 600; margin-bottom: 4px; }
  .sender-rule { position: absolute; left: 0; top: 172px; width: 204px; height: 2px; background: var(--burgundy); }

  .contact { position: absolute; left: 440px; top: 136px; list-style: none; font-size: 10.5px; color: var(--ink-soft); }
  .contact li { display: flex; align-items: center; gap: 9px; height: 17px; }
  .contact svg { width: 12px; height: 12px; flex: none; }
  .contact-rule { position: absolute; left: 440px; top: 211px; width: 239px; height: 2px; background: var(--burgundy); }

  .management { position: absolute; left: 440px; top: 223px; font-size: 10.5px; line-height: 17px; color: var(--ink-soft); }
  .management .person { font-weight: 600; color: var(--ink); }

  .footer-band {
    position: absolute; left: 0; top: 882px; width: 508px; height: 78px;
    background: var(--burgundy); color: var(--white);
    padding: 13px 0 0 66px; font-size: 8px; line-height: 20.5px;
  }
  .footer-band b { font-weight: 600; }
  .corner-square {
    position: absolute; left: 522px; top: 826px; width: 126px; height: 126px;
    border: 6px solid var(--silver); border-radius: 14px;
  }
</style>
</head>
<body>
  <main class="letterhead">
    <header class="brand">
      <div class="brand-square"></div>
      <div class="brand-name">
        <span class="firm">KLR BARSEN</span>
        <span class="trade">STEUERBERATUNG</span>
      </div>
    </header>

    <div class="fold-mark"></div>

    <div class="sender">
      <p class="company">KLR Barsen Steuerberatungsgesellschaft mbH</p>
      <p>Lindenweg 12 / 17489 Kransee</p>
    </div>
    <div class="sender-rule"></div>

    <ul class="contact">
      <li>
        <svg viewBox="0 0 12 12"><circle cx="6" cy="6" r="6" fill="#5e0d18"/><path d="M4 3.2l1 1.4-.6.7c.4.9 1 1.5 1.9 1.9l.7-.6 1.4 1-.6 1.1C5.6 8.5 3.5 6.4 3.3 4l.7-.8z" fill="#fff"/></svg>
        +49 (0) 3842 / 51 90 - 0
      </li>
      <li>
        <svg viewBox="0 0 12 12"><circle cx="6" cy="6" r="6" fill="#5e0d18"/><rect x="3" y="5" width="6" height="3.5" fill="#fff"/><rect x="4" y="3" width="4" height="2" fill="#fff"/></svg>
        +49 (0) 3842 / 51 90 - 14
      </li>
      <li>
        <svg viewBox="0 0 12 12"><circle cx="6" cy="6" r="6" fill="#5e0d18"/><rect x="3" y="4" width="6" height="4" fill="#fff"/><path d="M3 4l3 2.2L9 4" stroke="#5e0d18" stroke-width=".7" fill="none"/></svg>
        kontakt@kanzlei-mervato.de
      </li>
      <li>
        <svg viewBox="0 0 12 12"><circle cx="6" cy="6" r="6" fill="#5e0d18"/><circle cx="6" cy="6" r="2.8" fill="none" stroke="#fff" stroke-width=".8"/><path d="M3.2 6h5.6M6 3.2v5.6" stroke="#fff" stroke-width=".6"/></svg>
        www.kanzlei-mervato.de
      </li>
    </ul>
    <div class="contact-rule"></div>

    <div class="management">
      <p>Geschäftsführer:</p>
      <p class="person">Jonas Wellbrock - Teske</p>
      <p>Steuerberater / Dipl. Kaufmann</p>
      <p class="person">Peter Lindahl</p>
      <p>Steuerberater</p>
    </div>

    <footer class="footer-band">
      <p>KLR Barsen Steuerberatungsgesellschaft mbH · Lindenweg 12 · 17489 Kransee</p>
      <p><b>USt-IdNr.</b> DE000000000 · AG Hollmark · HRB 4187</p>
      <p>Sparkasse Musterstadt · <b>IBAN</b> DE00 0000 0000 0000 0000 00 · <b>BIC</b> XXXXDEM1XXX</p>
    </footer>
    <div class="corner-square"></div>
  </main>
</body>
</html>
```